Fenwick Grading LTD - website for irrigation & Landscape Lighting & Buried service wire

Looking for a website to help promote my business with Irrigation (installation, service, etc) and buried service wire/drainage solutions.

Commercial/Residential

Landscape lighting.

I’ll get photos in the trucks and trailers to upload as well maybe the machine as well.

Target Market(s)

Homeowners who want green grass and beautiful gardens. Beautiful landscape lighting

Industry/Entity Type

Irrigation systems and landscape lighting and buried service wire to homes and offering Drainage soltions.

Coding

Coded - Design and coding required

Number of Pages Required

4 page

Colors
F0912C
F2A743
F7CA91
FBE8D2
FDF5EE

Requirements
Must have
• was hoping to link up my email on fenwickgrading@mailbox-example.net with the website if possible.
Nice to have
• Page for Irrigation, page for landscape lighting, page buried service wire & drainage soltions.

```html
<!DOCTYPE html>
<html lang="en">
<head>
<meta charset="UTF-8">
<title>Fenwick Grading LTD</title>
<link href="https://fonts.googleapis.com/css2?family=Montserrat:wght@400;500;600&family=Roboto+Condensed:wght@700&display=swap" rel="stylesheet">
<style>
:root{
  --orange:#F0912C;
  --orange-2:#F2A743;
  --orange-3:#F7CA91;
  --cream:#FBE8D2;
  --ink:#111111;
  --body:#666666;
  --dark:#161616;
  --white:#ffffff;
}
*{margin:0;padding:0;box-sizing:border-box}
html,body{width:1200px;height:3120px;overflow:hidden;background:var(--white)}
body{position:relative;font-family:'Montserrat',sans-serif;color:var(--ink)}
.abs{position:absolute}

/* hero */
.hero{left:0;top:0;width:1200px;height:625px}
.hero svg{display:block}
.nav{top:28px;left:141px;width:918px;height:40px;display:flex;align-items:center;justify-content:space-between}
.brand{color:var(--orange);font-weight:600;font-size:22px;display:flex;align-items:center;gap:10px;white-space:nowrap}
.brand .dot{width:14px;height:14px;background:var(--orange)}
.menu{display:flex;align-items:center;gap:29px;font-size:12px;font-weight:500;color:var(--white);white-space:nowrap}
.menu .cta{background:var(--orange);padding:12px 20px}
.hero-title{left:141px;top:178px;width:480px;font-family:'Roboto Condensed',sans-serif;font-size:38px;line-height:48px;color:var(--white)}
.hero-text{left:142px;top:335px;width:450px;font-size:13px;line-height:22.5px;color:var(--white)}
.btn-square{left:141px;top:415px;background:var(--orange);color:var(--white);font-size:12px;font-weight:600;padding:12px 19px}

/* services */
.blob{width:390px;height:390px}
.svc-title{font-size:25px;font-weight:500;white-space:nowrap}
.svc-title span,.accent{color:var(--orange)}
.svc-lead{border-left:2px solid var(--orange);padding-left:11px;font-size:13px;line-height:23px;font-weight:500;margin-top:26px;width:400px}
.svc-text{font-size:13px;line-height:22.5px;color:var(--body);margin-top:24px;width:415px}
.btn-pill{display:inline-block;margin-top:28px;background:var(--orange);color:var(--white);font-size:12px;font-weight:600;letter-spacing:1px;padding:11px 19px;border-radius:20px}

/* testimonials */
.t-title{left:0;top:2124px;width:1200px;text-align:center;font-size:25px;font-weight:500}
.t-sub{left:0;top:2175px;width:1200px;text-align:center;font-size:13px;font-weight:500}
.quote{left:141px;top:2303px;width:475px;font-size:13px;line-height:22.5px;color:#333}
.quote-name{left:141px;top:2434px;font-size:16px;font-weight:500;color:var(--orange)}
.arrows{left:141px;top:2508px}
.avatar{border-radius:50%}

/* footer */
.footer{left:0;top:2690px;width:1200px;height:430px}
.f-brand{left:0;top:2815px;width:1200px;justify-content:center;font-size:30px}
.f-menu{left:0;top:2932px;width:1200px;justify-content:center;gap:33px;font-size:12px}
.rule{left:141px;width:918px;height:1px;background:#333}
.contact{top:3003px;display:flex;align-items:center;gap:14px;color:var(--white);font-size:13px;line-height:20px;white-space:nowrap}
.c-icon{width:36px;height:36px;border:1.5px solid var(--orange);border-radius:50%;display:flex;align-items:center;justify-content:center;flex:none}
.copy{left:141px;top:3082px;font-size:12px;color:#cfcfcf}
.socials{left:900px;top:3072px;display:flex;gap:8px}
.socials span{width:34px;height:34px;border:1.5px solid var(--orange);border-radius:50%;display:block}
</style>
</head>
<body>

<!-- hero -->
<div class="abs hero">
  <svg width="1200" height="625" viewBox="0 0 1200 625">
    <defs>
      <linearGradient id="heroFill" x1="0" y1="0" x2="1" y2="1">
        <stop offset="0" stop-color="#3e4a1e"/>
        <stop offset="0.5" stop-color="#55622a"/>
        <stop offset="1" stop-color="#2c2a1c"/>
      </linearGradient>
    </defs>
    <path d="M0 0H1200V540L600 618L0 540Z" fill="url(#heroFill)" role="img" aria-label="Photo of a landscaped garden lawn with path lights at dusk"/>
    <path d="M0 540L600 618L1200 540" fill="none" stroke="var(--orange)" stroke-width="4"/>
  </svg>
</div>
<div class="abs nav">
  <div class="brand"><span class="dot"></span>Fenwick Grading LTD</div>
  <div class="menu"><span>Home</span><span>Irrigation</span><span>Landscape Lighting</span><span>Service Wire &amp; Drainage</span><span class="cta">Contact Us</span></div>
</div>
<h1 class="abs hero-title">Transform Your Outdoor Space With Our Expert Irrigation And Lighting Solutions</h1>
<p class="abs hero-text">Get the perfect blend of form and function with our state-of-the-art irrigation systems and landscape lighting. Trust our experienced team to deliver buried service wire and drainage for your home</p>
<div class="abs btn-square">Contact Us</div>

<!-- service blob shape -->
<svg width="0" height="0" class="abs">
  <defs>
    <path id="blobShape" d="M180 6C245 0 300 45 338 115C372 180 365 255 300 295C240 332 160 355 90 365C32 373 2 330 10 270C18 205 40 150 60 100C82 48 125 12 180 6Z"/>
  </defs>
</svg>

<!-- irrigation -->
<svg class="abs blob" style="left:150px;top:700px" viewBox="0 0 390 390">
  <use href="#blobShape" fill="#7b95a8" role="img" aria-label="Photo of a sprinkler head spraying water over a field"/>
  <use href="#blobShape" transform="translate(10,4)" fill="none" stroke="var(--orange)" stroke-width="1.5"/>
</svg>
<div class="abs" style="left:638px;top:744px">
  <h2 class="svc-title">Irrigation <span>Systems</span></h2>
  <p class="svc-lead">Efficient and Effective Watering Solutions for Your Lawn and Garden</p>
  <p class="svc-text">Our irrigation systems are designed to provide your lawn and garden with the right amount of water, without wasting a single drop. With our expert installation and service, you can rest assured that your plants will receive the nourishment they need to thrive.</p>
  <span class="btn-pill">LEARN MORE</span>
</div>

<!-- lighting -->
<div class="abs" style="left:141px;top:1221px">
  <h2 class="svc-title">Landscape <span>Lighting</span></h2>
  <p class="svc-lead">Enhance Your Outdoor Space with Beautiful and Functional Lighting Solutions</p>
  <p class="svc-text">Our landscape lighting solutions are designed to enhance the beauty and functionality of your outdoor space. From subtle pathway lighting to dramatic spotlights, we'll work with you to create a lighting plan that meets your needs and complements your landscape.</p>
  <span class="btn-pill">LEARN MORE</span>
</div>
<svg class="abs blob" style="left:664px;top:1177px" viewBox="0 0 390 390">
  <use href="#blobShape" fill="#4a5a25" role="img" aria-label="Photo of a garden lit by a path light at dusk"/>
  <use href="#blobShape" transform="translate(10,4)" fill="none" stroke="var(--orange)" stroke-width="1.5"/>
</svg>

<!-- service wire & drainage -->
<svg class="abs blob" style="left:150px;top:1653px" viewBox="0 0 390 390">
  <use href="#blobShape" fill="#6e4a33" role="img" aria-label="Photo of a trench with buried service wire and drainage pipe"/>
  <use href="#blobShape" transform="translate(10,4)" fill="none" stroke="var(--orange)" stroke-width="1.5"/>
</svg>
<div class="abs" style="left:638px;top:1720px">
  <h2 class="svc-title">Service Wire <span>&amp; Drainage</span></h2>
  <p class="svc-lead">Buried Service Wire and Drainage Solutions for Your Property</p>
  <p class="svc-text">Our crew trenches and lays buried service wire to homes and businesses with precision and care. We also design and install drainage solutions that move water away from your lawn, garden and foundation, for residential and commercial properties.</p>
  <span class="btn-pill">LEARN MORE</span>
</div>

<!-- testimonials -->
<h2 class="abs t-title">What Our <span class="accent">Customers</span> Say</h2>
<p class="abs t-sub">Hear from Our Satisfied Clients</p>
<p class="abs quote">They maintain around 52 acres for us including several thousand sq ft or beds. Always answer thr phone and very prompt if we ever have an issue. Great guys all the way around! It is a long established fact that a reader will be distracted by the readable content of a page when looking at its layout.</p>
<p class="abs quote-name">Marcus Delaney</p>
<svg class="abs arrows" width="130" height="16" viewBox="0 0 130 16">
  <path d="M36 8H1M8 2L1 8L8 14" fill="none" stroke="#222" stroke-width="1.5"/>
  <path d="M92 8H127M120 2L127 8L120 14" fill="none" stroke="#222" stroke-width="1.5"/>
</svg>
<svg class="abs" style="left:708px;top:2230px" width="240" height="342" viewBox="0 0 240 342">
  <rect x="2" y="2" width="228" height="334" rx="114" fill="#8a929a" role="img" aria-label="Portrait photo of a featured customer"/>
  <path d="M116 6A114 114 0 0 1 236 120V222A114 114 0 0 1 116 338" fill="none" stroke="var(--orange)" stroke-width="1.5"/>
</svg>
<div class="abs avatar" style="left:945px;top:2183px;width:112px;height:112px;background:#a3564a" role="img" aria-label="Portrait photo of a customer"></div>
<div class="abs avatar" style="left:591px;top:2453px;width:80px;height:80px;background:#6d7a70" role="img" aria-label="Portrait photo of a customer"></div>
<div class="abs avatar" style="left:966px;top:2466px;width:70px;height:70px;background:#6a5a4c" role="img" aria-label="Portrait photo of a customer"></div>

<!-- footer -->
<svg class="abs footer" width="1200" height="430" viewBox="0 0 1200 430">
  <path d="M0 88L600 0L1200 88V430H0Z" fill="var(--dark)"/>
  <path d="M0 88L600 0L1200 88" fill="none" stroke="var(--orange)" stroke-width="8"/>
</svg>
<div class="abs brand f-brand"><span class="dot"></span>Fenwick Grading LTD</div>
<div class="abs menu f-menu"><span>Home</span><span>Irrigation</span><span>Landscape Lighting</span><span>Service Wire &amp; Drainage</span><span>Contact Us</span></div>
<div class="abs rule" style="top:2975px"></div>
<div class="abs contact" style="left:211px">
  <span class="c-icon"><svg width="14" height="18" viewBox="0 0 14 18"><path d="M7 1a6 6 0 0 0-6 6c0 4.5 6 10 6 10s6-5.5 6-10a6 6 0 0 0-6-6z" fill="none" stroke="#fff" stroke-width="1.6"/><circle cx="7" cy="7" r="2" fill="#fff"/></svg></span>
  <span>123, Building Name, Street<br>City, State XY 123456</span>
</div>
<div class="abs contact" style="left:500px">
  <span class="c-icon"><svg width="16" height="16" viewBox="0 0 16 16"><path d="M3 1l3 3-1.5 2a9 9 0 0 0 5.5 5.5L12 10l3 3-2 2C7 15 1 9 1 3z" fill="#fff"/></svg></span>
  <span><b style="font-weight:500">Phone</b><br>123-456-7890</span>
</div>
<div class="abs contact" style="left:730px">
  <span class="c-icon"><svg width="16" height="12" viewBox="0 0 16 12"><rect x="0" y="0" width="16" height="12" rx="1" fill="#fff"/><path d="M1 1l7 6 7-6" fill="none" stroke="var(--dark)" stroke-width="1.4"/></svg></span>
  <span><b style="font-weight:500">E-Mail</b><br>fenwickgrading@mailbox-example.net</span>
</div>
<div class="abs rule" style="top:3058px"></div>
<p class="abs copy">© 2024 Fenwick Grading LTD . All Rights Reserved.</p>
<div class="abs socials"><span></span><span></span><span></span><span></span></div>

</body>
</html>
```